Business Card Design needed for start up company Halvora

In need of a new business card designed for a start up company based in Sydney, Halvora is a new start up innovative Company, our mission it to make property accessible for everyday Australian and to become the leading Real Estate platform in Australia. We want it to be fresh and clean.

Industry/Entity Type

Financial

Contact Information for Business Card

Section for Name
Section for Title

HALVORA - The Strength of Pooling
Mobile:
Direct:

Font styles to use
Sans Serif

Colors
33a6d7
0692cd
0255a3
ffffff

Requirements
Must have
• Logo, all business card details

```html
<!DOCTYPE html>
<html lang="en">
<head>
<meta charset="utf-8">
<title>Halvora Business Card</title>
<link rel="stylesheet" href="https://fonts.googleapis.com/css2?family=Open+Sans:wght@400;600;700;800&display=swap">
<style>
  :root {
    --navy: #1f3f78;
    --sky: #2a9fd8;
    --white: #ffffff;
    --paper: #efefef;
    --stage: #e4e6ea;
  }
  * { margin: 0; padding: 0; box-sizing: border-box; }
  html, body {
    width: 1200px; height: 900px; overflow: hidden;
    background: var(--stage);
    font-family: "Open Sans", Arial, sans-serif;
  }
  .canvas { position: relative; width: 1200px; height: 900px; }

  .card { position: absolute; overflow: hidden; box-shadow: 0 4px 14px rgba(0,0,0,.12); }

  /* Front side */
  .card-front {
    left: 78px; top: 35px; width: 587px; height: 363px;
    background: var(--navy); color: var(--white);
  }
  .card-front .disc-outer {
    position: absolute; left: -40px; top: 6px;
    width: 340px; height: 340px; border-radius: 50%;
    background: var(--sky);
  }
  .card-front .disc {
    position: absolute; left: -13px; top: 30px;
    width: 302px; height: 302px; border-radius: 50%;
    background: var(--white);
  }
  .identity {
    position: absolute; right: 35px; top: 58px; text-align: right;
  }
  .identity .person-name {
    font-size: 21px; font-weight: 600; letter-spacing: .2px; line-height: 1.15;
  }
  .identity .person-title { font-size: 15px; font-weight: 400; line-height: 1.3; }

  .contact-list {
    position: absolute; right: 33px; top: 227px; list-style: none; text-align: right;
  }
  .contact-list li {
    display: flex; justify-content: flex-end; align-items: center; gap: 7px;
    font-size: 15px; line-height: 22px;
  }
  .contact-list svg { width: 13px; height: 13px; fill: var(--white); }

  /* Back side */
  .card-back {
    left: 388px; top: 505px; width: 567px; height: 352px;
    background: var(--paper);
  }
  .brand {
    position: absolute; left: 98px; top: 122px;
    display: flex; align-items: center; gap: 14px;
  }
  .brand .brand-dot {
    width: 112px; height: 112px; border-radius: 50%; background: var(--sky);
  }
  .brand .brand-name {
    font-size: 58px; font-weight: 800; color: var(--navy); letter-spacing: -.5px;
  }
  .tagline {
    position: absolute; left: 0; right: 0; top: 249px; text-align: center;
    font-size: 17px; font-weight: 600; color: var(--navy); letter-spacing: .3px;
  }
</style>
</head>
<body>
<div class="canvas">
  <section class="card card-front">
    <div class="disc-outer"></div>
    <div class="disc"></div>
    <div class="identity">
      <div class="person-name">MARCUS ELLERY</div>
      <div class="person-title">Managing Director</div>
    </div>
    <ul class="contact-list">
      <li>044-870 312 645
        <svg viewBox="0 0 16 16" aria-hidden="true"><path d="M2 5c0-2 2-3 6-3s6 1 6 3v1h-3V5H5v1H2zM4 7h8l2 6H2zM8 8.5a2 2 0 1 0 0 4 2 2 0 0 0 0-4z"/></svg>
      </li>
      <li>044-870 312 645
        <svg viewBox="0 0 16 16" aria-hidden="true"><path d="M4 1h8v14H4zM5.5 3v9h5V3zM8 12.8a.8.8 0 1 0 0 1.6.8.8 0 0 0 0-1.6z"/></svg>
      </li>
      <li>hello@halvora.com
        <svg viewBox="0 0 16 16" aria-hidden="true"><path d="M1 3h14v10H1zM2.5 4.5 8 9l5.5-4.5v-.2h-11z"/></svg>
      </li>
      <li>www.halvora.com
        <svg viewBox="0 0 16 16" aria-hidden="true"><circle cx="8" cy="8" r="7"/><path d="M5 4c1 1 2 1 2 2s-1 1-1 2 1 2 0 3M10 10c1-1 2 0 3-1" stroke="#1f3f78" stroke-width="1.3" fill="none"/></svg>
      </li>
    </ul>
  </section>

  <section class="card card-back">
    <div class="brand">
      <div class="brand-dot"></div>
      <div class="brand-name">HALVORA</div>
    </div>
    <p class="tagline">THE STRENGTH OF POOLING</p>
  </section>
</div>
</body>
</html>
```